KBT Business Cards

We require business cards for our business. We would like a matte black back to the card, with our logo centred in the middle. The front side of the card is open to design.

Target Market(s)

Clients looking for legal services (professional)

Industry/Entity Type

Legal

Contact Information for Business Card

Doran Kelbrath
Partner
Mobile: 0461 738 524
Email: doran@kbtlaw.co
Website: www.kbtlaw.co
Level 3, 118 Wendmore Street
Sydney NSW 2000

Font styles to use
Other font styles liked:
• Avenir

Colors
f04a50
ffffff
1b1b1b

Requirements
Must have
• Black back with logo included in the centre of the card.
• Our font is Avenir.

```html
<!DOCTYPE html>
<html lang="en">
<head>
<meta charset="utf-8">
<title>KBT Business Cards</title>
<link href="https://fonts.googleapis.com/css2?family=Roboto:wght@400;500;700&display=swap" rel="stylesheet">
<style>
  :root {
    --backdrop: #8a8a8a;
    --paper: #ffffff;
    --ink: #1b1b1b;
    --accent: #b5123a;
    --accent-bright: #d8234f;
    --matte: #231f20;
    --light-text: #ececec;
    --rule: #1b1b1b;
  }
  * { box-sizing: border-box; margin: 0; padding: 0; }
  html, body {
    width: 1200px; height: 1200px; overflow: hidden;
    background: var(--backdrop);
    font-family: "Roboto", Arial, sans-serif;
  }
  .stage { position: relative; width: 1200px; height: 1200px; }
  .card {
    position: absolute; top: 310px; width: 364px; height: 594px;
    box-shadow: 2px 3px 6px rgba(0,0,0,0.45);
  }
  .card--front { left: 234px; background: var(--paper); color: var(--ink); }
  .card--back { left: 630px; width: 367px; background: var(--matte); }

  .brand {
    position: absolute; left: 62px; top: 462px; top: 152px;
    display: flex; align-items: center; gap: 20px;
  }
  .brand__mark { width: 40px; height: 40px; background: var(--accent); flex: none; }
  .brand__name {
    font-size: 27px; font-weight: 400; line-height: 28px;
    color: var(--ink); text-transform: uppercase; letter-spacing: -0.2px;
  }

  .contact {
    position: absolute; left: 0; right: 0; top: 356px;
    text-align: center; font-size: 17px; line-height: 22px;
  }
  .contact__name { color: var(--accent); font-weight: 500; font-size: 21px; line-height: 24px; text-transform: uppercase; }
  .contact__role { line-height: 18px; }
  .contact__rule { width: 150px; height: 1px; background: var(--rule); margin: 10px auto 10px; }
  .contact__label { color: var(--accent); font-weight: 500; }
  .contact__web { color: var(--accent); font-weight: 700; font-size: 16px; }
  .contact__address { margin-top: 0; }

  .back__name {
    position: absolute; left: 44px; top: 345px;
    font-size: 50px; line-height: 52px; font-weight: 500;
    color: var(--light-text); text-transform: uppercase;
  }
  .back__web {
    position: absolute; left: 0; right: 0; top: 530px;
    text-align: center; color: var(--accent-bright);
    font-size: 17px; font-weight: 700;
  }
</style>
</head>
<body>
<div class="stage">
  <section class="card card--front">
    <div class="brand">
      <span class="brand__mark"></span>
      <p class="brand__name">Kelbrath<br>Borthway<br>Legal</p>
    </div>
    <div class="contact">
      <p class="contact__name">Doran Kelbrath</p>
      <p class="contact__role">Partner</p>
      <div class="contact__rule"></div>
      <p><span class="contact__label">M:</span> 0461 738 524</p>
      <p><span class="contact__label">E:</span> doran@kbtlaw.co</p>
      <p class="contact__web">www.kbtlaw.co</p>
      <div class="contact__rule"></div>
      <p class="contact__address">Level 3, 118 Wendmore<br>Street, Sydney NSW 2000</p>
    </div>
  </section>

  <section class="card card--back">
    <p class="back__name">Kelbrath<br>Borthway<br>Legal</p>
    <p class="back__web">www.kbtlaw.co</p>
  </section>
</div>
</body>
</html>
```